Business Card Design

I am an Event and Wedding Planner in need of an eye catching business card featuring my logo (attached), my contact details, and my company tagline (Making every celebration glow with wonder...) I would like the tagline in font similar the logo's font.
Updates
I have just noticed that my logo has a misspelling so for the final design, I will be uploading a corrected logo as soon as I have it.
My apologies.
Reason: Waiting on a corrected logo...Lantern is misspelled and it should say Weddings not Wedding
The logo has been corrected so now Lantern is spelled correctly and it says Weddings instead of Wedding. Please use Edwardian Script ITC as the font for the tagline so it will match the logo. Thank you for your patience.
Target Market(s)
Engaged couples and people hosting milestone celebrations. 25-50 years old, predominately female
Industry/Entity Type
Business
Contact Information for Business Card
Rosalind Merrow, Event Manager / Owner, Mobile: 0491 868 254, Email: rosalind@velvetlanternco.com.au, www.velvetlanternco.com.au, Making every celebration glow with wonder...

```html
<!DOCTYPE html>
<html lang="en">
<head>
<meta charset="utf-8">
<title>Velvet Lantern – Business Card</title>
<link href="https://fonts.googleapis.com/css2?family=Montserrat:wght@400;500;700&family=Pinyon+Script&display=swap" rel="stylesheet">
<style>
  :root {
    --bg: #e9e7e4;
    --card: #ffffff;
    --ink: #1c1c1c;
    --ink-soft: #555555;
    --accent: #c8353b;
    --band: #0f0f0f;
    --rule: #bdbdbd;
  }
  * { box-sizing: border-box; margin: 0; padding: 0; }
  html, body {
    width: 1200px; height: 899px; overflow: hidden;
    background: var(--bg);
    font-family: "Montserrat", sans-serif;
    color: var(--ink);
  }
  .sheet {
    position: relative; width: 1200px; height: 899px;
    display: flex; align-items: center; justify-content: center; gap: 60px;
  }
  .card {
    position: relative; width: 520px; height: 297px;
    background: var(--card); border-radius: 26px; overflow: hidden;
    box-shadow: 0 8px 24px rgba(0,0,0,.12);
  }
  .tagline {
    font-family: "Pinyon Script", cursive;
    color: var(--ink); white-space: nowrap;
  }
  /* Front */
  .card-front .waves { position: absolute; inset: 0; width: 100%; height: 100%; }
  .brand {
    position: absolute; left: 48px; top: 56px;
    display: flex; align-items: center; gap: 12px;
  }
  .brand-name {
    font-family: "Montserrat", sans-serif; font-weight: 500;
    font-size: 30px; color: var(--ink); letter-spacing: .5px;
  }
  .brand-dot { width: 12px; height: 12px; border-radius: 50%; background: var(--accent); }
  .brand-rule {
    position: absolute; left: 48px; top: 106px; width: 230px; height: 1px;
    background: var(--rule);
  }
  .front-tagline {
    position: absolute; left: 48px; top: 112px;
    font-size: 22px; line-height: 1.2;
  }
  .front-web {
    position: absolute; right: 30px; bottom: 14px;
    color: #ffffff; font-size: 12px; letter-spacing: 2.4px;
  }
  /* Back */
  .back-brand {
    position: absolute; left: 0; right: 0; top: 22px;
    display: flex; justify-content: center; align-items: center; gap: 8px;
  }
  .back-brand .brand-name { font-size: 17px; }
  .back-brand .brand-dot { width: 7px; height: 7px; }
  .back-tagline {
    position: absolute; left: 0; right: 0; top: 46px;
    text-align: center; font-size: 15px; line-height: 1.2;
  }
  .details { position: absolute; left: 180px; top: 90px; }
  .person-name { font-weight: 700; font-size: 17px; letter-spacing: 1.4px; text-transform: uppercase; }
  .person-title { font-size: 11px; color: var(--ink-soft); margin-top: 2px; }
  .address { font-size: 11px; color: var(--ink-soft); margin-top: 18px; line-height: 1.45; }
  .contact-list { list-style: none; margin-top: 16px; }
  .contact-list li {
    display: flex; align-items: center; gap: 9px;
    font-size: 10px; color: var(--ink-soft); line-height: 1.9;
  }
  .contact-list svg { width: 11px; height: 11px; fill: var(--ink-soft); flex: none; }
</style>
</head>
<body>
<main class="sheet">

  <section class="card card-front" aria-label="Card front">
    <svg class="waves" viewBox="0 0 520 297" preserveAspectRatio="none" aria-hidden="true">
      <path d="M0 168 C 150 222, 340 236, 520 228 L520 297 L0 297 Z" fill="var(--band)"/>
      <path d="M0 150 C 150 206, 340 222, 520 214 L520 228 C 340 236, 150 222, 0 168 Z" fill="var(--accent)"/>
    </svg>
    <div class="brand">
      <span class="brand-name">Velvet Lantern</span>
      <span class="brand-dot"></span>
    </div>
    <div class="brand-rule"></div>
    <p class="tagline front-tagline">Making every celebration glow with wonder...</p>
    <p class="front-web">www.velvetlanternco.com.au</p>
  </section>

  <section class="card card-back" aria-label="Card back">
    <div class="back-brand">
      <span class="brand-name">Velvet Lantern</span>
      <span class="brand-dot"></span>
    </div>
    <p class="tagline back-tagline">Making every celebration glow with wonder...</p>
    <div class="details">
      <h1 class="person-name">Rosalind Merrow</h1>
      <p class="person-title">Event Manager / Owner</p>
      <p class="address">12 Harbour Lane Level 3<br>Fitzroy VIC</p>
      <ul class="contact-list">
        <li>
          <svg viewBox="0 0 24 24"><path d="M6.6 10.8a15.1 15.1 0 0 0 6.6 6.6l2.2-2.2a1 1 0 0 1 1-.25 11.4 11.4 0 0 0 3.6.57 1 1 0 0 1 1 1V20a1 1 0 0 1-1 1A17 17 0 0 1 3 4a1 1 0 0 1 1-1h3.5a1 1 0 0 1 1 1c0 1.25.2 2.450.57 3.57a1 1 0 0 1-.25 1z"/></svg>
          0491 868 254
        </li>
        <li>
          <svg viewBox="0 0 24 24"><path d="M7 1h10a2 2 0 0 1 2 2v18a2 2 0 0 1-2 2H7a2 2 0 0 1-2-2V3a2 2 0 0 1 2-2zm0 3v14h10V4zm5 15.5a1 1 0 1 0 0 2 1 1 0 0 0 0-2z"/></svg>
          0491 868 254
        </li>
        <li>
          <svg viewBox="0 0 24 24"><path d="M2 5h20v14H2zm2 2v.5l8 5 8-5V7zm0 3v7h16v-7l-8 5z"/></svg>
          rosalind@velvetlanternco.com.au
        </li>
        <li>
          <svg viewBox="0 0 24 24"><path d="M12 2a10 10 0 1 0 0 20 10 10 0 0 0 0-20zm0 2c.9 0 2.2 1.9 2.7 5H9.3C9.8 5.9 11.1 4 12 4zM4.3 11h3c0 .7 0 1.4.1 2H4.3a8 8 0 0 1 0-2zm5 0h5.4a16 16 0 0 1 0 2H9.3a16 16 0 0 1 0-2zm7.4 0h3a8 8 0 0 1 0 2h-3c.1-.6.1-1.3 0-2zM9.3 15h5.4c-.5 3.1-1.8 5-2.7 5s-2.2-1.9-2.7-5z"/></svg>
          www.velvetlanternco.com.au
        </li>
      </ul>
    </div>
  </section>

</main>
</body>
</html>
```